VelkaVision.com

Complete Website Design (Godaddy) and company Branding / Logo Design. The products will sell are only done in-person and are installed. So this site does not need to be an e-commerce site. We will only be giving out information and collecting customer inquires. Website will only need to be about 3 to 5 pages.

```html
<!DOCTYPE html>
<html lang="en">
<head>
<meta charset="utf-8">
<title>VelkaVision</title>
<link href="https://fonts.googleapis.com/css2?family=Montserrat:wght@600;700&family=Poppins:wght@300;400;500;600&display=swap" rel="stylesheet">
<style>
:root{
  --navy:#253150;
  --navy-btn:#27335a;
  --band:#3b4870;
  --maroon:#5a2429;
  --ink:#161616;
  --link:#1a3fc4;
  --footer:#1b1b1b;
  --muted:#8a8a8a;
  --rule:#3b466a;
}
*{margin:0;padding:0;box-sizing:border-box}
html,body{width:686px;height:1200px;overflow:hidden;background:#fff}
body{position:relative;font-family:'Poppins',sans-serif;color:var(--ink)}
.abs{position:absolute}
.heading{font-family:'Montserrat',sans-serif;font-weight:700}

.hero{left:0;top:0;width:686px;height:367px;
  background:radial-gradient(ellipse 30% 40% at 50% 38%,#2a2520 0%,#4a4540 45%,rgba(0,0,0,0) 75%),
  linear-gradient(180deg,#e8e8ea 0%,#dcdcde 70%,#9a9894 96%,#6e6b67 100%);}
.logo{left:63px;top:20px;font-size:21px;color:#111}
.nav-link{top:29px;font-size:9px;font-weight:500}
.nav-home{left:450px;color:var(--link);font-weight:600}
.nav-about{left:499px;color:#222}
.nav-cta{left:556px;top:22px;width:66px;height:25px;background:var(--navy-btn);color:#fff;border-radius:2px;
  font-size:8px;font-weight:600;display:flex;align-items:center;justify-content:center}
.hero-title{left:0;width:766px;top:108px;text-align:center;font-size:28px;color:#f2f2f2}
.hero-btn{left:354px;top:153px;width:65px;height:25px;background:var(--navy-btn);border:1px solid #cfd4e2;border-radius:2px;
  color:#fff;font-size:8px;font-weight:600;display:flex;align-items:center;justify-content:center}

.about{left:0;top:367px;width:686px;height:275px;
  background:radial-gradient(ellipse 35% 55% at 62% 55%,#34477e 0%,rgba(52,71,126,0) 70%),linear-gradient(90deg,#39456a,#3c4972 50%,#3a476e)}
.scroll-arrow{left:337px;top:350px}
.about-title{left:100px;top:440px;font-size:16px;color:#fff}
.about-text{left:100px;top:468px;width:234px;font-size:8.3px;line-height:13.6px;color:#fff;text-align:justify}
.stat{left:421px;color:#fff}
.stat b{display:block;font-family:'Montserrat',sans-serif;font-weight:700;font-size:22px;line-height:24px}
.stat span{display:block;font-size:8.3px;line-height:11.5px;margin-top:3px}

.contact-card{left:66px;top:691px;width:274px;height:291px;background:var(--navy)}
.contact-title{left:112px;top:734px;font-size:16px;color:#fff}
.info-icon{left:112px;width:25px;height:25px;border-radius:50%;background:#eceef2;display:flex;align-items:center;justify-content:center}
.info-label{left:149px;font-size:9.5px;font-weight:300;color:#fff}
.info-value{left:149px;font-size:9.5px;font-weight:400;color:#fff;line-height:14.5px}
.social{top:919px;width:25px;height:25px;border:1.2px solid #fff;border-radius:50%}

.field{left:356px;width:262px;border-bottom:1px solid var(--rule);font-size:7.5px;color:var(--muted);padding-left:11px}
.send{left:356px;top:911px;width:66px;height:25px;background:var(--maroon);color:#fff;border-radius:2px;
  font-size:8px;font-weight:600;display:flex;align-items:center;justify-content:center}

.footer{left:0;top:1032px;width:686px;height:168px;background:var(--footer)}
.footer-logo{left:0;width:686px;top:1077px;text-align:center;font-size:21px;color:#fff}
.footer-link{top:1118px;font-size:9px;font-weight:500;color:#fff}
.footer-rule{left:64px;top:1147px;width:558px;height:1px;background:#d8d8d8}
.copyright{left:0;width:696px;top:1160px;text-align:center;font-size:8px;color:#ddd}
</style>
</head>
<body>

<div class="abs hero" role="img" aria-label="Photo of two installers mounting a flat-screen TV between wall speakers"></div>
<div class="abs logo heading">VelkaVision</div>
<div class="abs nav-link nav-home">Home</div>
<div class="abs nav-link nav-about">About Us</div>
<div class="abs nav-cta">CONTACT US</div>
<div class="abs hero-title heading">VelkaVision</div>
<div class="abs hero-btn">GET STARTED</div>

<div class="abs about" role="img" aria-label="Background photo of a technician working, under a blue overlay"></div>
<svg class="abs scroll-arrow" width="12" height="44" viewBox="0 0 12 44"><path d="M6 0V42M1 36L6 42L11 36" fill="none" stroke="#9aa0ae" stroke-width="1"/></svg>
<div class="abs about-title heading">About Us</div>
<p class="abs about-text">Karspiciatis unde omnis iste natus error sisaet voluptatem accusantium doloremque laudantium, totam rsesesdf em aperiam, eaque ipsa quae aseb illo inventore veritatis et quasi architecto beatae vitae dicta sunt explicabo. Nemo enim ipsam voluptatem quia voluptas sit aspernatur aut odit aut fugit, sed quia consequuntur magni dolores eos qui ratione voluptatem seqsaeui nesciunt. Neque porro quisquam est, qsesui dolorem ipsum quia dolor sit amet, consectetur, adipisci velit, sed quia non numquam eius modi tempora incidunt ut labore et dolore magnam.</p>
<div class="abs stat" style="top:414px"><b>20</b><span>Kaseui aseasei msael seioase<br>uaskeu ascmwe sadosei</span></div>
<div class="abs stat" style="top:480px"><b>13</b><span>Kaseui aseasei msael seioase<br>uaskeu ascmwe sadosei</span></div>
<div class="abs stat" style="top:547px"><b>08</b><span>Kaseui aseasei msael seioase<br>uaskeu ascmwe sadosei</span></div>

<div class="abs contact-card"></div>
<div class="abs contact-title heading">Contact Us</div>

<div class="abs info-icon" style="top:777px"><svg width="11" height="13" viewBox="0 0 11 13"><path d="M5.5 0.5A4.5 4.5 0 0 0 1 5c0 3.3 4.5 7.5 4.5 7.5S10 8.3 10 5A4.5 4.5 0 0 0 5.5 0.5z" fill="var(--navy)"/><circle cx="5.5" cy="5" r="1.7" fill="#eceef2"/></svg></div>
<div class="abs info-label" style="top:773px">Address</div>
<div class="abs info-value" style="top:787px">48 Alder Creek Rd<br>Brookfield, NC 27512</div>

<div class="abs info-icon" style="top:829px"><svg width="12" height="12" viewBox="0 0 12 12"><path d="M2.6 0.8l1.8 2.3-1 1.3c.7 1.5 2 2.8 3.5 3.5l1.3-1 2.3 1.8-.9 2c-4.6-.3-8.4-4.1-8.7-8.7z" fill="var(--navy)"/></svg></div>
<div class="abs info-label" style="top:826px">Call Us</div>
<div class="abs info-value" style="top:838px">555-014-2290</div>

<div class="abs info-icon" style="top:871px"><svg width="13" height="9" viewBox="0 0 13 9"><rect x="0.6" y="0.6" width="11.8" height="7.8" fill="none" stroke="var(--navy)" stroke-width="1.1"/><path d="M0.6 0.6L6.5 5.2L12.4 0.6M0.6 8.4L5 4.2M12.4 8.4L8 4.2" fill="none" stroke="var(--navy)" stroke-width="1.1"/></svg></div>
<div class="abs info-label" style="top:869px">Email</div>
<div class="abs info-value" style="top:881px">info@velkavision.com</div>

<div class="abs social" style="left:112px"></div>
<div class="abs social" style="left:143px"></div>
<div class="abs social" style="left:174px"></div>

<div class="abs field" style="top:734px;height:19px">Your Name</div>
<div class="abs field" style="top:768px;height:19px">Email</div>
<div class="abs field" style="top:803px;height:19px">Phone Number</div>
<div class="abs field" style="top:837px;height:57px">Message</div>
<div class="abs send">SEND MESSAGE</div>

<div class="abs footer"></div>
<div class="abs footer-logo heading">VelkaVision</div>
<div class="abs footer-link" style="left:265px">Home</div>
<div class="abs footer-link" style="left:314px">About Us</div>
<div class="abs footer-link" style="left:375px">Contact Us</div>
<div class="abs footer-rule"></div>
<div class="abs copyright">© 2024. All rights reserved.</div>

</body>
</html>
```